A card that says it all!

Hey there!
We are in need of a business card design for a facility service provider company named Dovra Works.
I would like a business card design that is not focus on a person but more on the company. A place for a QR code would be nice, and i will have that code direct to our request form online. "Scanner to schedule service" or "Scan to schedule a estimate". Something like that. Dovra Works is the Industry Leader in Facility Remodeling, Rollouts, and Capital Repairs

Target Market(s)

large facilities needing services such as remodels. HVAC, plumbing, electrical

Industry/Entity Type

Industry Leader in Facility Remodeling, Rollouts, and Capital Repairs

Contact Information for Business Card

phone number: 517.382.9064; email: info@dovraworks.example; Website: www.DovraWorks.example

Requirements
Must have
• sleak; classic
Should not have
• No houses or tools art

```html
<!DOCTYPE html>
<html lang="en">
<head>
<meta charset="utf-8">
<title>Dovra Works — Business Card</title>
<link rel="stylesheet" href="https://fonts.googleapis.com/css2?family=Bodoni+Moda:opsz,wght@6..96,400&family=Poppins:wght@600&display=swap">
<style>
  :root {
    --card-blue: #17489c;
    --ink-white: #ffffff;
    --accent-red: #e0262b;
    --qr-text: #17489c;
  }
  html, body {
    margin: 0;
    padding: 0;
    width: 1200px;
    height: 686px;
    overflow: hidden;
    background: var(--card-blue);
  }
  .card {
    position: relative;
    width: 1200px;
    height: 686px;
    background: var(--card-blue);
    color: var(--ink-white);
    font-family: "Bodoni Moda", "Times New Roman", serif;
    font-weight: 400;
  }
  .company-name {
    position: absolute;
    left: 72px;
    top: 58px;
    margin: 0;
    font-weight: 400;
    line-height: 1;
    white-space: nowrap;
  }
  .company-name .name-lead { font-size: 74px; letter-spacing: -1px; }
  .company-name .name-tail { font-size: 46px; }
  .tagline {
    position: absolute;
    left: 72px;
    top: 157px;
    margin: 0;
    font-size: 34px;
    line-height: 51px;
    white-space: nowrap;
  }
  .brand-mark {
    position: absolute;
    right: 53px;
    top: 62px;
    font-size: 44px;
    line-height: 1;
    white-space: nowrap;
  }
  .contact-list {
    position: absolute;
    left: 169px;
    top: 462px;
    margin: 0;
    padding: 0;
    list-style: none;
    font-size: 40px;
    line-height: 57px;
  }
  .qr-slot {
    position: absolute;
    left: 869px;
    top: 351px;
    width: 278px;
    height: 278px;
    box-sizing: border-box;
    background: var(--ink-white);
    border: 3px solid var(--accent-red);
    display: flex;
    align-items: center;
    justify-content: center;
    text-align: center;
    font-family: "Poppins", Arial, sans-serif;
    font-weight: 600;
    font-size: 50px;
    line-height: 1.15;
    color: var(--qr-text);
  }
</style>
</head>
<body>
  <main class="card">
    <h1 class="company-name"><span class="name-lead">Dovra</span> <span class="name-tail">Works</span></h1>
    <p class="tagline">is the Industry Leader in Facility<br>Remodeling, Rollouts, and<br>Capital Repairs</p>
    <div class="brand-mark">Dovra Works</div>
    <ul class="contact-list">
      <li>517.382.9064</li>
      <li>info@dovraworks.example</li>
      <li>www.DovraWorks.example</li>
    </ul>
    <div class="qr-slot">QR<br>CODE</div>
  </main>
</body>
</html>
```